Upland Bird Hunting Preserve and Pointing Dog kennel

Need Price packages outlined for the bird hunting business. List the kennel and that we provide training and dogs for sale.
The preserve is "Tall Heron Provisions" the dog kennel is "Pine Hollow Setters"
1/2 Day Upland Field Hunts: 5 Pheasants $120
7 Chukar $125
Continental Hunt 12 Pheasants $325 includes meal, minimum 12 hunters
Guides available $100

Target Market(s)

upland bird hunters

Industry/Entity Type

hunting, outdoor

Colors
EE7325
F08F49
F5BC92
FAE3D3
FDF4ED

```html
<!DOCTYPE html>
<html lang="en">
<head>
<meta charset="utf-8">
<title>Tall Heron Provisions – Hunting Packages</title>
<link href="https://fonts.googleapis.com/css2?family=Sora:wght@400;500;600;700;800&display=swap" rel="stylesheet">
<style>
  :root {
    --backdrop: #f1d8d2;
    --paper: #f8f8f8;
    --ink: #111111;
    --orange: #e2562a;
    --blush: #fae3d3;
    --red: #c8102e;
    --grey-box: #e7e7e7;
    --photo-dark: #6f6a5c;
    --photo-light: #a9a592;
  }
  * { box-sizing: border-box; margin: 0; padding: 0; }
  html, body {
    width: 1200px; height: 2167px; overflow: hidden;
    background: var(--backdrop);
    font-family: "Sora", sans-serif; color: var(--ink);
  }
  .flyer {
    position: absolute; left: 49px; top: 370px;
    width: 1002px; height: 1297px;
    background: var(--paper);
    transform: scale(1.1); transform-origin: top left;
    box-shadow: 0 2px 6px rgba(0,0,0,0.12);
  }
  .flyer > * { position: absolute; }

  .hero-illustration {
    left: 60px; top: 60px; width: 195px; height: 235px;
    background: linear-gradient(160deg, #d9d9d9, #9c9c9c);
    border-radius: 6px;
  }
  .brand-name {
    left: 295px; top: 52px;
    font-size: 64px; font-weight: 800; line-height: 60px; letter-spacing: -1px;
    text-transform: uppercase;
  }
  .location {
    left: 295px; top: 186px; display: flex; align-items: center; gap: 10px;
    font-size: 38px; font-weight: 600; line-height: 44px;
  }
  .location svg { width: 28px; height: 40px; }
  .license-band {
    left: 292px; top: 239px; width: 651px; height: 60px;
    background: var(--orange); border-radius: 4px;
    color: #fff; font-size: 30px; font-weight: 600;
    display: flex; align-items: center; padding-left: 20px;
  }

  .packages {
    left: 58px; top: 327px; width: 885px; height: 299px;
    border: 2px solid var(--ink); border-radius: 14px;
  }
  .packages-title {
    position: absolute; top: 26px; width: 100%; text-align: center;
    font-size: 34px; font-weight: 700;
  }
  .price-list { position: absolute; left: 193px; top: 77px; width: 497px; list-style: none; }
  .price-row {
    display: flex; align-items: baseline; gap: 14px;
    font-size: 31px; line-height: 40px;
  }
  .price-row .leader { flex: 1; border-bottom: 2px dashed #333; transform: translateY(-6px); }
  .price-row .price { width: 82px; }
  .guide-pill {
    position: absolute; left: 141px; top: 212px; width: 600px; height: 52px;
    background: var(--blush); border-radius: 8px;
    display: flex; align-items: center; justify-content: center;
    font-size: 26px; font-weight: 500;
  }

  .offer { font-size: 23px; line-height: 30px; }
  .offer h3 { font-size: 23px; font-weight: 800; margin-bottom: 8px; }
  .offer p + p { margin-top: 8px; }
  .continental { left: 58px; top: 652px; width: 420px; }
  .notes {
    left: 58px; top: 820px; width: 413px; height: 83px;
    background: var(--grey-box); border-radius: 8px;
    padding: 12px 18px; font-size: 19.5px; font-weight: 500; line-height: 29px;
  }
  .big-game { left: 533px; top: 652px; width: 420px; }
  .big-game h3 { color: var(--red); }
  .big-game p + h3 { margin-top: 18px; }

  .kennel-name {
    left: 58px; top: 1020px; width: 337px;
    display: flex; align-items: center; gap: 14px;
    font-size: 30px; font-weight: 600;
  }
  .kennel-name .dot { width: 22px; height: 22px; border-radius: 50%; background: var(--ink); flex: none; }

  .contact { left: 533px; top: 955px; width: 215px; font-size: 25px; font-weight: 700; line-height: 30px; }
  .contact .rule { height: 2px; background: var(--red); margin: 14px 0 16px; }
  .bird-photo {
    left: 766px; top: 955px; width: 180px; height: 180px; border-radius: 8px;
    background: linear-gradient(170deg, var(--photo-light), var(--photo-dark));
  }
  .blank-panel {
    left: 58px; top: 1168px; width: 885px; height: 70px;
    border: 2px solid var(--ink); border-radius: 10px;
  }
</style>
</head>
<body>
<main class="flyer">
  <div class="hero-illustration" role="img" aria-label="Ink sketch of a hunter in a field with flushing pheasants"></div>

  <h1 class="brand-name">Tall Heron<br>Provisions, LLC</h1>
  <div class="location">
    <svg viewBox="0 0 28 40" aria-hidden="true">
      <circle cx="14" cy="11" r="10" fill="#e03030"/>
      <rect x="12.5" y="18" width="3" height="21" rx="1.5" fill="#9a9a9a"/>
    </svg>
    <span>ASHFORD, MO</span>
  </div>
  <div class="license-band">LICENSED SHOOTING PRESERVE</div>

  <section class="packages">
    <h2 class="packages-title">Hunting Packages – ½ Day Hunts</h2>
    <ul class="price-list">
      <li class="price-row"><span>5 Pheasants</span><span class="leader"></span><span class="price">$120</span></li>
      <li class="price-row"><span>7 Chukar</span><span class="leader"></span><span class="price">$125</span></li>
      <li class="price-row"><span>8 Quail</span><span class="leader"></span><span class="price">$100</span></li>
    </ul>
    <div class="guide-pill">GUIDE AVAILABLE $100 PER HALF DAY</div>
  </section>

  <section class="offer continental">
    <h3>Continental Pheasant Hunt</h3>
    <p>12 Hunter Minimum</p>
    <p>$325 per hunter, includes<br>12 birds per hunter &amp; meal.</p>
  </section>
  <div class="notes">All hunts include bird cleaning<br>Lodging available, call for pricing</div>

  <section class="offer big-game">
    <h3>Guided Spring Turkey Hunts</h3>
    <p>3 Day Hunt includes meals<br>&amp; lodging – $1600</p>
    <h3>Guided Whitetail Deer Hunts<br>– Rifle &amp; Archery</h3>
    <p>5 Day Hunt includes meals<br>&amp; lodging – $2750</p>
  </section>

  <div class="kennel-name"><span class="dot"></span><span>Pine Hollow Setters</span></div>

  <div class="contact">
    <p>Dale Whitcomb<br>555-014-2867</p>
    <div class="rule"></div>
    <p>Puppies and<br>started dogs<br>available!</p>
  </div>
  <div class="bird-photo" role="img" aria-label="Photo of a chukar partridge standing on a rock among grass"></div>

  <div class="blank-panel"></div>
</main>
</body>
</html>
```